TA BRAMLEY BUSINESS CARD DESIGN PROJECT

We need to utilize our logo that was expertly created on PixelHarbor and now need to match this with a business card design.

```html
<!DOCTYPE html>
<html lang="en">
<head>
<meta charset="utf-8">
<title>TA Bramley Business Card</title>
<link href="https://fonts.googleapis.com/css2?family=Open+Sans:wght@400;700&display=swap" rel="stylesheet">
<style>
  :root {
    --backdrop: #dcdddf;
    --card: #f3f3f1;
    --brand-blue: #0b55b3;
    --edge-blue: #1155d0;
    --text-grey: #8a8a8a;
    --rule-grey: #dadad6;
  }
  * { margin: 0; padding: 0; box-sizing: border-box; }
  html, body {
    width: 1200px; height: 1051px; overflow: hidden;
    background: var(--backdrop);
    font-family: "Open Sans", Arial, sans-serif;
  }
  .card {
    position: absolute; left: 300px;
    width: 600px; height: 343px;
    background: var(--card);
    border-bottom: 4px solid var(--edge-blue);
    box-shadow: 0 12px 30px rgba(0,0,0,0.12);
  }
  .card--front { top: 150px; }
  .card--back { top: 558px; }

  .brand-name {
    font-weight: 700;
    color: var(--brand-blue);
    letter-spacing: 0.08em;
    white-space: nowrap;
  }
  .card--front .brand-name {
    position: absolute; left: 40px; top: 150px; font-size: 30px;
  }
  .card--back .brand-name {
    position: absolute; left: 0; right: 0; top: 142px;
    text-align: center; font-size: 46px;
  }

  .divider {
    position: absolute; left: 300px; top: 60px;
    width: 2px; height: 220px; background: var(--rule-grey);
  }
  .contact {
    position: absolute; left: 330px; top: 68px;
    color: var(--text-grey); font-size: 13.5px; line-height: 1.5;
  }
  .contact__name {
    color: var(--brand-blue); font-weight: 700; font-size: 19px;
    letter-spacing: 0.02em; line-height: 1.2;
  }
  .contact__role { margin-bottom: 14px; }
  .contact__address { margin-bottom: 14px; }
  .contact__line { display: flex; align-items: center; gap: 7px; }
  .contact__line svg { width: 11px; height: 11px; fill: var(--text-grey); flex: none; }
</style>
</head>
<body>
  <section class="card card--front">
    <div class="brand-name">TA BRAMLEY</div>
    <div class="divider"></div>
    <div class="contact">
      <div class="contact__name">DARA WHITCOMBE</div>
      <div class="contact__role">President</div>
      <div class="contact__address">1580 Cove Landing Way<br>Seal Bay CA 90412</div>
      <div class="contact__line">
        <svg viewBox="0 0 12 12" aria-hidden="true"><path d="M2.5 1l2 2.2-1 1.3a7 7 0 0 0 4 4l1.3-1 2.2 2-1.3 1.5C5 11 1 7 1 2.3z"/></svg>
        <span>555-014-2287</span>
      </div>
      <div class="contact__line">
        <svg viewBox="0 0 12 12" aria-hidden="true"><path d="M1 3h10v6H1z M1 3l5 3.5L11 3" fill="none" stroke="#8a8a8a" stroke-width="1.3"/></svg>
        <span>d.whitcombe@tabramley.com</span>
      </div>
      <div class="contact__line">
        <svg viewBox="0 0 12 12" aria-hidden="true"><circle cx="6" cy="6" r="5"/><path d="M1 6h10M6 1c2 2 2 8 0 10M6 1c-2 2-2 8 0 10" fill="none" stroke="#f3f3f1" stroke-width="0.9"/></svg>
        <span>www.tabramley.com</span>
      </div>
    </div>
  </section>

  <section class="card card--back">
    <div class="brand-name">TA BRAMLEY</div>
  </section>
</body>
</html>
```